Business Card for Industrial Distributor

We need a business card design for an industrial distributor. We sell machine parts for the manufacturing and oil industry. We would like the cards to look clean and modern but with a touch of industry.

Our colors are blue/white.

Please feel free to visit our website www.korvelpartsco.com

Target Market(s)

mexican manufacturers in the automobile/aerospace industry

Industry/Entity Type

Industrial

Colors
ffffff
0555a3

```html
<!DOCTYPE html>
<html lang="en">
<head>
<meta charset="utf-8">
<title>Korvel Business Card</title>
<link rel="stylesheet" href="https://fonts.googleapis.com/css2?family=Arimo:wght@400;700&display=swap">
<style>
  :root {
    --page: #2b2623;
    --card: #161718;
    --brand-blue: #2b3fc4;
    --brand-blue-deep: #0555a3;
    --text-white: #ffffff;
    --text-grey: #b9bcc2;
    --rule: #7d8087;
  }
  * { box-sizing: border-box; margin: 0; padding: 0; }
  html, body {
    width: 1200px; height: 864px; overflow: hidden;
    background: var(--page);
    font-family: "Arimo", Arial, sans-serif;
  }
  .stage { position: relative; width: 1200px; height: 864px; }
  .card {
    position: absolute; top: 280px;
    width: 530px; height: 303px;
    background: var(--card);
    box-shadow: 0 10px 24px rgba(0,0,0,.45);
  }
  /* front */
  .card-front { left: 40px; }
  .front-mark {
    position: absolute; left: 150px; top: 62px;
    display: flex; align-items: center; gap: 18px;
  }
  .front-mark .dot {
    width: 120px; height: 120px; border-radius: 50%;
    background: radial-gradient(circle at 40% 35%, #3f57d6, var(--brand-blue) 60%, #1d2c94);
  }
  .front-mark .name {
    font-size: 44px; font-weight: 700; color: var(--brand-blue);
  }
  .front-url {
    position: absolute; left: 70px; top: 222px;
    font-size: 13px; letter-spacing: 5px; color: var(--text-grey);
  }
  /* back */
  .card-back { left: 630px; }
  .person { position: absolute; left: 34px; top: 36px; }
  .person-name {
    font-size: 17px; color: var(--brand-blue); letter-spacing: .3px;
  }
  .person-title { font-size: 15px; color: var(--text-white); margin-top: 3px; }
  .rule {
    position: absolute; left: 104px; top: 78px;
    width: 410px; height: 1px; background: var(--rule);
    transform-origin: left center; transform: rotate(14deg);
  }
  .contacts { position: absolute; left: 34px; top: 90px; list-style: none; }
  .contacts li {
    display: flex; align-items: center; gap: 8px;
    font-size: 13px; color: var(--text-white); height: 20px;
  }
  .contacts svg { width: 12px; height: 12px; fill: var(--brand-blue); flex: none; }
  .back-mark {
    position: absolute; right: 26px; top: 34px;
    display: flex; align-items: center; gap: 8px;
  }
  .back-mark .dot {
    width: 34px; height: 34px; border-radius: 50%; background: var(--brand-blue);
  }
  .back-mark .name { font-size: 34px; font-weight: 700; color: var(--brand-blue); }
  .address {
    position: absolute; right: 30px; bottom: 30px;
    text-align: right; font-size: 13px; line-height: 19px; color: var(--text-white);
  }
</style>
</head>
<body>
<main class="stage">
  <section class="card card-front">
    <div class="front-mark">
      <span class="dot"></span>
      <span class="name">Korvel</span>
    </div>
    <p class="front-url">www.korvelpartsco.com</p>
  </section>

  <section class="card card-back">
    <div class="person">
      <p class="person-name">MARCO RUELAS</p>
      <p class="person-title">President</p>
    </div>
    <span class="rule"></span>
    <ul class="contacts">
      <li><svg viewBox="0 0 12 12"><path d="M2 1h2l1 3-1.3 1a6 6 0 0 0 3.3 3.3L8 7l3 1v2c0 .6-.4 1-1 1A9 9 0 0 1 1 2c0-.6.4-1 1-1z"/></svg>(555) 014 - 2210</li>
      <li><svg viewBox="0 0 12 12"><path d="M3 1h6v3H3zM1 5h10v5H9V8H3v2H1zM3 9h6v2H3z"/></svg>(555) 014 - 2214</li>
      <li><svg viewBox="0 0 12 12"><path d="M1 3h10v6H1zM1.5 3.5 6 7l4.5-3.5" stroke="#161718" stroke-width=".8"/></svg>sales@korvelpartsco.com</li>
      <li><svg viewBox="0 0 12 12"><circle cx="6" cy="6" r="5"/><path d="M1 6h10M6 1c2 2.5 2 7.5 0 10M6 1c-2 2.5-2 7.5 0 10" stroke="#161718" stroke-width=".8" fill="none"/></svg>www.korvelpartsco.com</li>
    </ul>
    <div class="back-mark">
      <span class="dot"></span>
      <span class="name">Korvel</span>
    </div>
    <address class="address" style="font-style:normal">
      Korvel International Corp<br>
      4180 Harlan Ridge Rd<br>
      Eastport,TX 70014
    </address>
  </section>
</main>
</body>
</html>
```